Business Card Design

We need a business card designed for our new company. Prefer a black card with white logo & writing.

Contact Information for Business Card

Ted Galloway, address: 7-4812 Fernhollow Road, Abbotsford, BC, V3K 8R2, Office Phone: 604-712-3390, Cell: 604-947-2164, Email: ted@resinworkshub.ca

Colors

Designer to choose only greyscale colors for use in the design.

```html
<!DOCTYPE html>
<html lang="en">
<head>
<meta charset="utf-8">
<title>Resinworks Hub – Business Card</title>
<link href="https://fonts.googleapis.com/css2?family=Poppins:wght@300;400;500;700;800&display=swap" rel="stylesheet">
<style>
  :root {
    --backdrop: #1e1e1e;
    --card: #2a2a2a;
    --card-back: #232323;
    --ink: #ffffff;
    --ink-soft: #d9d9d9;
    --band: #f2f2f2;
    --band-ink: #1a1a1a;
    --rule: #8a8a8a;
    --grey-light: #bdbdbd;
    --grey-mid: #7a7a7a;
  }
  * { box-sizing: border-box; margin: 0; padding: 0; }
  html, body {
    width: 1200px; height: 780px; overflow: hidden;
    background: var(--backdrop);
    font-family: "Poppins", sans-serif;
  }
  .sheet {
    position: relative; width: 1200px; height: 780px;
    display: flex; align-items: center; justify-content: center; gap: 60px;
  }
  .card {
    position: relative; width: 520px; height: 298px;
    border-radius: 6px; overflow: hidden;
    box-shadow: 0 18px 40px rgba(0,0,0,.45);
  }

  /* Front */
  .card--front { background: var(--card); color: var(--ink); }
  .brand-mark {
    position: absolute; left: 46px; top: 58px; width: 190px;
    text-align: center;
  }
  .brand-name {
    font-weight: 800; font-size: 30px; line-height: 1.02;
    letter-spacing: .5px; color: var(--ink); text-transform: uppercase;
  }
  .divider { position: absolute; left: 0; top: 0; width: 520px; height: 298px; pointer-events: none; }
  .identity { position: absolute; left: 300px; top: 54px; }
  .person-name { font-size: 30px; line-height: 1.05; white-space: nowrap; }
  .person-name .first { font-weight: 800; }
  .person-name .last { font-weight: 300; }
  .person-title { font-size: 13px; font-weight: 400; color: var(--ink-soft); margin-top: 2px; }
  .contacts { list-style: none; margin-top: 14px; }
  .contacts li {
    display: flex; align-items: center; gap: 8px;
    font-size: 12.5px; font-weight: 300; line-height: 20px; color: var(--ink-soft);
  }
  .contacts svg { width: 12px; height: 12px; flex: none; }
  .address-band {
    position: absolute; left: 0; bottom: 26px; height: 28px; width: 398px;
    background: var(--band); color: var(--band-ink);
    clip-path: polygon(0 0, 384px 0, 398px 50%, 384px 100%, 0 100%);
    display: flex; align-items: center; padding-left: 22px;
    font-size: 12px; font-weight: 500; white-space: nowrap;
  }
  .corner-accent {
    position: absolute; right: 0; bottom: 0; width: 118px; height: 84px;
    background: linear-gradient(135deg, var(--grey-mid), var(--grey-light) 55%, var(--ink));
    clip-path: polygon(40% 0, 100% 30%, 100% 100%, 0 100%, 0 45%);
    opacity: .85;
  }

  /* Back */
  .card--back { background: var(--card-back); }
  .pattern-field {
    position: absolute; inset: 0;
    background: radial-gradient(ellipse at 70% 30%, #3a3a3a 0%, #2a2a2a 45%, #1f1f1f 100%);
  }
  .back-brand {
    position: absolute; inset: 0;
    display: flex; align-items: center; justify-content: center;
  }
  .back-brand .brand-name { font-size: 40px; text-align: center; }
</style>
</head>
<body>
<main class="sheet">

  <section class="card card--front" aria-label="Business card front">
    <div class="brand-mark">
      <div class="brand-name">Resinworks<br>Hub</div>
    </div>

    <svg class="divider" viewBox="0 0 520 298" aria-hidden="true">
      <line x1="262" y1="228" x2="300" y2="44" stroke="var(--rule)" stroke-width="1"/>
    </svg>

    <div class="identity">
      <h1 class="person-name"><span class="first">Ted</span> <span class="last">Galloway</span></h1>
      <p class="person-title">Founder &amp; CEO</p>
      <ul class="contacts">
        <li>
          <svg viewBox="0 0 24 24" aria-hidden="true"><path fill="var(--ink)" d="M6.6 10.8a15 15 0 0 0 6.6 6.6l2.2-2.2c.3-.3.7-.4 1-.2 1.1.4 2.3.6 3.6.6.6 0 1 .4 1 1V20c0 .6-.4 1-1 1A17 17 0 0 1 3 4c0-.6.4-1 1-1h3.5c.6 0 1 .4 1 1 0 1.3.2 2.5.6 3.6.1.3 0 .7-.2 1z"/></svg>
          604-712-3390
        </li>
        <li>
          <svg viewBox="0 0 24 24" aria-hidden="true"><rect x="6" y="2" width="12" height="20" rx="2" fill="none" stroke="var(--ink)" stroke-width="2"/><circle cx="12" cy="18" r="1.3" fill="var(--ink)"/></svg>
          604-947-2164
        </li>
        <li>
          <svg viewBox="0 0 24 24" aria-hidden="true"><g fill="none" stroke="var(--ink)" stroke-width="2"><circle cx="12" cy="12" r="9"/><path d="M3 12h18M12 3c3 3 3 15 0 18M12 3c-3 3-3 15 0 18"/></g></svg>
          www.resinworkshub.ca
        </li>
        <li>
          <svg viewBox="0 0 24 24" aria-hidden="true"><g fill="none" stroke="var(--ink)" stroke-width="2"><rect x="3" y="5" width="18" height="14" rx="1.5"/><path d="M3 6l9 7 9-7"/></g></svg>
          ted@resinworkshub.ca
        </li>
      </ul>
    </div>

    <div class="address-band">7-4812 Fernhollow Road, Abbotsford, BC, V3K 8R2.</div>
    <div class="corner-accent" role="img" aria-label="Stacked grey diamond accent shapes"></div>
  </section>

  <section class="card card--back" aria-label="Business card back">
    <div class="pattern-field" role="img" aria-label="Subtle repeating tonal brand pattern across the card"></div>
    <div class="back-brand">
      <div class="brand-name">Resinworks<br>Hub</div>
    </div>
  </section>

</main>
</body>
</html>
```